Menu Board

Hi Maribel,

I would like you to design for me a menu board for all my products.

The layout I have hand drawn for you so just follow my layout.

Pho
Noodle salads
Rice
StirFry with Thick Rice Noodles
Spring Rolls Ricepaper Rolls

Poster Size: AO Vertical ( 841W x 1189H)

There are more photos of the rice dishes but I thought I can send this through so you can start and I can send you the rest of the photos when I get back from my photographer.

I will have items descriptions to follow also

• Here are the rest of the photos >

```html
<!DOCTYPE html>
<html lang="en">
<head>
<meta charset="utf-8">
<title>Menu Board</title>
<link rel="stylesheet" href="https://fonts.googleapis.com/css2?family=Varela+Round&display=swap">
<style>
  :root {
    --page: #e9e9e7;
    --board-red: #d42a2a;
    --cell-line: #b81f1f;
    --bar-black: #222222;
    --header-black: #262626;
    --text-light: #ffffff;
    --plate-edge: #1c1c1c;
  }
  * { box-sizing: border-box; margin: 0; padding: 0; }
  html, body {
    width: 1200px; height: 800px; overflow: hidden;
    background: var(--page);
    font-family: "Varela Round", sans-serif;
  }
  .menu-board {
    position: absolute; left: 330px; top: 20px;
    width: 540px; height: 760px;
    background: var(--board-red);
    display: flex; flex-direction: column;
    box-shadow: 0 2px 10px rgba(0,0,0,.18);
  }
  .board-header {
    height: 80px; background: var(--header-black);
    color: var(--text-light);
    display: flex; align-items: center; justify-content: center;
    font-size: 20px; letter-spacing: .5px;
  }
  .menu-row { display: grid; }
  .row-pho { grid-template-columns: repeat(3, 1fr); height: 150px; }
  .row-four { grid-template-columns: repeat(4, 1fr); height: 118px; }
  .row-rolls { grid-template-columns: 0.55fr 1fr 1fr 0.45fr; flex: 1; }
  .menu-item {
    display: flex; flex-direction: column;
    border-right: 1px solid var(--cell-line);
    border-bottom: 1px solid var(--cell-line);
  }
  .menu-item:last-child { border-right: none; }
  .item-photo-area {
    flex: 1; display: flex; align-items: center; justify-content: center;
  }
  .dish-photo {
    border-radius: 50%;
    border: 3px solid var(--plate-edge);
    background: radial-gradient(circle at 45% 45%, #e8c27a 0%, #b8793e 55%, #f2efe8 72%, #ffffff 100%);
  }
  .row-pho .dish-photo { width: 76px; height: 76px; }
  .row-four .dish-photo { width: 54px; height: 54px; }
  .row-rolls .dish-photo { width: 72px; height: 72px; }
  .photo-greens { background: radial-gradient(circle at 45% 45%, #c9d38a 0%, #7f9a4a 55%, #f2efe8 72%, #fff 100%); }
  .photo-pale { background: radial-gradient(circle at 45% 45%, #f1e6c8 0%, #c7d6a6 55%, #f5f2ea 72%, #fff 100%); }
  .item-label {
    background: var(--bar-black); color: var(--text-light);
    text-align: center; white-space: nowrap; overflow: hidden;
  }
  .row-pho .item-label { height: 32px; line-height: 32px; font-size: 15px; }
  .row-four .item-label { height: 24px; line-height: 24px; font-size: 8.5px; }
  .row-rolls .item-label { height: 34px; line-height: 34px; font-size: 12px; }
  .row-rolls .edge-cell { border-bottom: none; }
</style>
</head>
<body>
<main class="menu-board">
  <header class="board-header">Menu Board</header>

  <section class="menu-row row-pho">
    <div class="menu-item"><div class="item-photo-area"><div class="dish-photo photo-greens" role="img" aria-label="Photo of a bowl of beef pho"></div></div><div class="item-label">Beef Pho</div></div>
    <div class="menu-item"><div class="item-photo-area"><div class="dish-photo photo-greens" role="img" aria-label="Photo of a bowl of chicken pho"></div></div><div class="item-label">Chicken Pho</div></div>
    <div class="menu-item"><div class="item-photo-area"><div class="dish-photo" role="img" aria-label="Photo of a bowl of tofu pho"></div></div><div class="item-label">Tofu Pho</div></div>
  </section>

  <section class="menu-row row-four">
    <div class="menu-item"><div class="item-photo-area"><div class="dish-photo" role="img" aria-label="Photo of beef noodle salad"></div></div><div class="item-label">Beef Noodle salads</div></div>
    <div class="menu-item"><div class="item-photo-area"><div class="dish-photo photo-greens" role="img" aria-label="Photo of chicken noodle salad"></div></div><div class="item-label">Chicken Noodle salads</div></div>
    <div class="menu-item"><div class="item-photo-area"><div class="dish-photo" role="img" aria-label="Photo of BBQ pork noodle salad"></div></div><div class="item-label">BBQ Pork Noodle salads</div></div>
    <div class="menu-item"><div class="item-photo-area"><div class="dish-photo" role="img" aria-label="Photo of tofu noodle salad"></div></div><div class="item-label">Tofu Noodle salads</div></div>
  </section>

  <section class="menu-row row-four">
    <div class="menu-item"><div class="item-photo-area"></div><div class="item-label">Beef Rice</div></div>
    <div class="menu-item"><div class="item-photo-area"></div><div class="item-label">Chicken Rice</div></div>
    <div class="menu-item"><div class="item-photo-area"></div><div class="item-label">Tofu Rice</div></div>
    <div class="menu-item"><div class="item-photo-area"><div class="dish-photo photo-pale" role="img" aria-label="Photo of a plate of fried rice"></div></div><div class="item-label">Fried Rice</div></div>
  </section>

  <section class="menu-row row-four">
    <div class="menu-item"><div class="item-photo-area"></div><div class="item-label"></div></div>
    <div class="menu-item"><div class="item-photo-area"></div><div class="item-label">Chicken StirFry Noodles</div></div>
    <div class="menu-item"><div class="item-photo-area"></div><div class="item-label">Tofu StirFry Noodles</div></div>
    <div class="menu-item"><div class="item-photo-area"></div><div class="item-label">StirFry with Thick Rice Noodles</div></div>
  </section>

  <section class="menu-row row-rolls">
    <div class="menu-item edge-cell"></div>
    <div class="menu-item"><div class="item-photo-area"><div class="dish-photo" role="img" aria-label="Photo of fried spring rolls with dipping sauce"></div></div><div class="item-label">Spring Rolls</div></div>
    <div class="menu-item"><div class="item-photo-area"><div class="dish-photo photo-pale" role="img" aria-label="Photo of fresh ricepaper rolls"></div></div><div class="item-label">Ricepaper Rolls</div></div>
    <div class="menu-item edge-cell"></div>
  </section>
</main>
</body>
</html>
```